Granite Tile Retail Website

We need wireframe PSD for a website selling granite tile. There are 4 custom pages, shopping cart page, and checkout page. I have a logo designed but the color scheme is up to you.
Color Gallery - We have approximately 20 different stone colors. Each color will have a little gallery of its own pictures. On this page the customer can also add a sample piece of the color they are viewing to their shopping cart.
Questions Page - This page has 3 elements
1. Upload or fax diagram of kitchen for quotation
2. Installation video
3. Installation FAQ (text)
Order Page - This page has 3 steps for the customer
1. Customer chooses his color.
2. For each color we have numerous different products. He inputs the quantity of each product.
3. Customer is given total price and shipping quote. If order over $500 it says "This order qualifies for free shipping". Customer can click on button to "Order Now"
Shopping Cart - Very standard, just like I have attached here. Just modify for your colors / font.
Checkout - Just like in the attached. See design-explanation.docx for minor adjustments.
I have vector file for logo.
Updates
Please try to post your designs by tonightÂ
Target Market(s)
Home owners 40-60 years old
Industry/Entity Type
Shopping
Look and feel

```html
<!DOCTYPE html>
<html lang="en">
<head>
<meta charset="utf-8">
<title>Easy Stone – Questions</title>
<link rel="stylesheet" href="https://fonts.googleapis.com/css2?family=Oswald:wght@400;500&family=Nunito+Sans:wght@400;600&display=swap">
<style>
  :root {
    --bg: #f3f3f3;
    --paper: #ffffff;
    --band: #f2f2f2;
    --ink: #222222;
    --ink-soft: #3a3a3a;
    --heading: #3b3b3b;
    --brand: #5a1522;
    --accent: #e8a21c;
    --accent-light: #f6c24a;
    --accent-dark: #b97a08;
    --line: #cfcfcf;
    --frame: #b8b8b8;
  }
  * { box-sizing: border-box; margin: 0; padding: 0; }
  html, body { width: 953px; height: 1200px; overflow: hidden; background: var(--bg); }
  body { font-family: "Nunito Sans", Arial, sans-serif; color: var(--ink); position: relative; }
  .page { position: absolute; left: 35px; top: 35px; width: 882px; height: 1122px; background: var(--paper); border: 1px solid #e2e2e2; }
  .abs { position: absolute; }
  .cond { font-family: "Oswald", "Arial Narrow", sans-serif; text-transform: uppercase; }

  /* header */
  .site-header { left: 53px; top: 56px; width: 847px; height: 106px; background: linear-gradient(#ffffff, var(--band)); border-top: 1px solid #e4e4e4; border-bottom: 1px solid #dcdcdc; }
  .brand { left: 79px; top: 87px; display: flex; align-items: center; gap: 10px; font-family: "Nunito Sans", sans-serif; font-weight: 600; font-size: 30px; color: var(--brand); letter-spacing: 1px; }
  .brand-mark { width: 26px; height: 26px; background: var(--accent); }
  .main-nav { right: 53px; top: 84px; display: flex; height: 52px; align-items: center; }
  .main-nav a { font-family: "Oswald", sans-serif; font-size: 19px; color: var(--heading); text-decoration: none; padding: 0 10px; line-height: 52px; border-left: 1px solid #9a9a9a; text-transform: uppercase; }
  .main-nav a:first-child { border-left: none; }
  .main-nav a.active { color: var(--accent); }

  /* left column */
  .fax-intro { left: 62px; top: 198px; width: 396px; text-align: center; font-size: 24px; line-height: 27px; font-weight: 600; color: var(--ink); }
  .fax-box { left: 106px; top: 290px; width: 303px; height: 46px; background: linear-gradient(var(--accent-light), var(--accent)); border: 2px solid var(--accent-dark); font-size: 29px; line-height: 42px; text-align: center; color: #2a1a00; font-weight: 500; }
  .sample-label { top: 371px; font-size: 12.5px; width: 190px; text-align: center; }
  .diagram { top: 395px; width: 191px; height: 137px; border: 3px solid #c9c9c9; background: linear-gradient(#fafafa, #e6e6e6); }
  .form-label { left: 62px; font-size: 15.5px; color: var(--ink-soft); }
  .field { height: 28px; border: 1px solid var(--line); background: linear-gradient(#f4f4f4, #ffffff); }
  .browse { position: absolute; right: 0; top: 0; width: 69px; height: 26px; border-left: 1px solid var(--line); background: linear-gradient(#fafafa, #e6e6e6); font-size: 15px; line-height: 26px; text-align: center; color: #333; }
  .send-btn { left: 218px; top: 718px; width: 215px; height: 50px; background: linear-gradient(var(--accent-light), var(--accent)); border: 2px solid var(--accent-dark); display: flex; align-items: center; gap: 10px; padding-left: 11px; font-size: 25px; color: #2a1a00; font-weight: 500; }

  .section-title { font-family: "Oswald", sans-serif; font-size: 23px; color: var(--heading); text-transform: uppercase; letter-spacing: -0.3px; }
  .faq-col { top: 829px; width: 407px; font-size: 11.6px; line-height: 16.8px; color: #333; text-align: justify; }
  .faq-col p { text-indent: 32px; }

  /* right column */
  .video { left: 485px; top: 279px; width: 416px; height: 253px; background: #000; }
  .video-frame { position: absolute; left: 0; top: 0; width: 416px; height: 230px; background: radial-gradient(ellipse at 55% 55%, #9c6b52 0%, #6e2a22 35%, #1a0d3a 70%, #0b0720 100%); }
  .video-bar { position: absolute; left: 0; bottom: 0; width: 416px; height: 23px; background: linear-gradient(#2b2b2b, #111); color: #ddd; font-size: 8px; font-family: Arial, sans-serif; }
  .diagram-list { left: 486px; top: 615px; font-size: 14.5px; line-height: 17px; padding-left: 14px; }
  .diagram-list li { padding-left: 4px; }

  /* footer */
  .site-footer { left: 53px; top: 1043px; width: 847px; height: 114px; background: linear-gradient(var(--band), #fafafa); border-top: 1px solid #dcdcdc; }
  .foot-col { top: 1057px; list-style: none; font-family: "Oswald", sans-serif; font-size: 12.5px; line-height: 17px; color: var(--brand); text-transform: uppercase; letter-spacing: -0.2px; }
  .foot-col .active { color: var(--accent); }
  .badge-circle { left: 699px; top: 1061px; width: 62px; height: 50px; border-radius: 50%; background: #d8c46a; }
  .badge-rect { left: 772px; top: 1061px; width: 101px; height: 38px; background: #1f5a8c; border-radius: 3px; }
  .badge-bar { left: 772px; top: 1104px; width: 101px; height: 26px; background: #cfd9e6; border-radius: 3px; }
</style>
</head>
<body>
<div class="page"></div>

<header>
  <div class="abs site-header"></div>
  <div class="abs brand"><span class="brand-mark"></span><span>EASY STONE</span></div>
  <nav class="abs main-nav">
    <a href="#">Home</a><a href="#">Gallery</a><a href="#" class="active">Questions</a><a href="#">Order</a><a href="#">Shopping Cart</a>
  </nav>
</header>

<main>
  <h1 class="abs fax-intro">Need help Calculating<br>how much Stone do you need?<br>Send us a Diagram!</h1>
  <div class="abs fax-box cond">Fax:&nbsp;&nbsp;&nbsp;800-555-0142</div>

  <div class="abs sample-label" style="left:63px">Sample diagram 1</div>
  <div class="abs sample-label" style="left:257px">Sample diagram 2</div>
  <div class="abs diagram" style="left:66px" role="img" aria-label="Sample kitchen floor plan diagram"></div>
  <div class="abs diagram" style="left:265px" role="img" aria-label="Sample kitchen floor plan diagram"></div>

  <form>
    <label class="abs form-label" style="top:550px">Upload your Diagram</label>
    <div class="abs field" style="left:217px;top:547px;width:216px"><span class="browse cond">Browse</span></div>
    <label class="abs form-label" style="top:590px">Name</label>
    <div class="abs field" style="left:110px;top:586px;width:323px"></div>
    <label class="abs form-label" style="top:630px">Phone</label>
    <div class="abs field" style="left:114px;top:625px;width:319px"></div>
    <label class="abs form-label" style="top:670px">E-mail</label>
    <div class="abs field" style="left:117px;top:665px;width:316px"></div>
    <div class="abs send-btn cond">
      <svg width="30" height="30" viewBox="0 0 30 30"><circle cx="15" cy="15" r="14" fill="#2b2b2b"/><path d="M8.5 15.5l4.5 4.5 8.5-9" stroke="#fff" stroke-width="3" fill="none" stroke-linecap="round"/></svg>
      <span>Send Diagram</span>
    </div>
  </form>

  <h2 class="abs section-title" style="left:62px;top:786px">FAQ</h2>
  <div class="abs faq-col" style="left:62px">
    <p>Lorem ipsum dolor sit amet, consectetuer adipiscing elit. Aenean commodo ligula eget dolor. Aenean massa. Cum sociis natoque penatibus et magnis dis parturient montes, nascetur ridiculus mus. Donec quam felis, ultricies nec, pellentesque eu, pretium quis, sem. Nulla consequat massa quis enim. Donec pede justo, fringilla vel, aliquet nec, vulputate eget, arcu. In enim justo, rhoncus ut, imperdiet a, venenatis vitae, justo.</p>
    <p>Nullam dictum felis eu pede mollis pretium. Integer tincidunt. Cras dapibus. Vivamus elementum semper nisi. Donec quam felis, ultricies nec, pellentesque eu, pretium quis, sem. Nulla consequat massa quis enim.</p>
  </div>
  <div class="abs faq-col" style="left:485px">
    <p>Lorem ipsum dolor sit amet, consectetuer adipiscing elit. Aenean commodo ligula eget dolor. Aenean massa. Cum sociis natoque penatibus et magnis dis parturient montes, nascetur ridiculus mus. Donec quam felis, ultricies nec, pellentesque eu, pretium quis, sem. Nulla consequat massa quis enim. Donec pede justo, fringilla vel, aliquet nec, vulputate eget, arcu. In enim justo, rhoncus ut, imperdiet a, venenatis vitae, justo.</p>
    <p>Nullam dictum felis eu pede mollis pretium. Integer tincidunt. Cras dapibus. Vivamus elementum semper nisi. Donec quam felis, ultricies nec, pellentesque eu, pretium quis, sem. Nulla consequat massa quis enim.</p>
  </div>

  <h2 class="abs section-title" style="left:486px;top:243px">Instalation Video</h2>
  <div class="abs video">
    <div class="video-frame" role="img" aria-label="Installation video still of a speaker in a red chair"></div>
    <div class="video-bar">
      <svg width="416" height="23" viewBox="0 0 416 23">
        <rect x="18" y="2" width="340" height="3" fill="#555"/>
        <rect x="18" y="2" width="8" height="3" fill="#c33"/>
        <circle cx="22" cy="3.5" r="3.5" fill="#ddd"/>
        <path d="M16 10l8 5-8 5z" fill="#ccc"/>
        <path d="M44 13h3l4-3v10l-4-3h-3z" fill="#ccc"/>
        <text x="65" y="18" fill="#fff" font-size="8" font-family="Arial">0:06 / 2:26</text>
        <text x="353" y="18" fill="#ccc" font-size="8" font-family="Arial">360p</text>
      </svg>
    </div>
  </div>

  <h2 class="abs section-title" style="left:486px;top:569px">Instalation Diagrams</h2>
  <ol class="abs diagram-list">
    <li>Backerboard + Plywood</li>
    <li>Inside Corner 1</li>
    <li>Inside Corner 2</li>
    <li>Ogee Edge 1</li>
    <li></li>
    <li></li>
    <li></li>
  </ol>
</main>

<footer>
  <div class="abs site-footer"></div>
  <ul class="abs foot-col" style="left:80px">
    <li>Home</li><li>Gallery</li><li class="active">Questions</li><li>Order</li><li>Shopping Cart</li>
  </ul>
  <ul class="abs foot-col" style="left:268px">
    <li>Return Policy</li><li>Shipping Policy</li><li>Privacy</li><li>Terms of Use</li><li>Customer Service</li>
  </ul>
  <ul class="abs foot-col" style="left:476px">
    <li>New Link</li><li>Another Link</li><li>Third Link</li><li>Fourth Link</li><li>Fifth Link</li>
  </ul>
  <div class="abs badge-circle" role="img" aria-label="Payment processor verification badge"></div>
  <div class="abs badge-rect" role="img" aria-label="Business accreditation badge"></div>
  <div class="abs badge-bar" role="img" aria-label="Secure payment badge"></div>
</footer>
</body>
</html>
```